Looking for a modern, Professional business card design

We have a simple business card, but are looking for a more modern, professional look. A sample of the basic card is attached as well as the logo. We would also like to add that we offer:
Struggling with your finances?
- Learn to become debt free
- Discover the power of cash
- Control your money instead of it controlling you
Let us help you achieve a new level of financial freedom!
Also, we would like to have a "SPECIAL OFFER!: FREE 30 minute consultation"
Financial Planning

```html
<!DOCTYPE html>
<html lang="en">
<head>
<meta charset="utf-8">
<title>Steadfast Money Coaching – Business Card</title>
<link href="https://fonts.googleapis.com/css2?family=Josefin+Sans:wght@400;600;700&family=Russo+One&display=swap" rel="stylesheet">
<style>
  :root {
    --bg: #e6e8e6;
    --card: #ffffff;
    --lime: #8cc63f;
    --green: #3a9a3f;
    --ink: #1c1c1c;
    --rule: #b9b9b9;
  }
  * { box-sizing: border-box; margin: 0; padding: 0; }
  html, body { width: 1200px; height: 900px; overflow: hidden; }
  body {
    background: var(--bg);
    font-family: "Josefin Sans", sans-serif;
    color: var(--ink);
    position: relative;
  }
  .card {
    position: absolute;
    width: 540px;
    height: 310px;
    background: var(--card);
    border-radius: 22px;
    overflow: hidden;
    box-shadow: 0 14px 30px rgba(0,0,0,.18);
  }
  .card-front { left: 60px; top: 120px; }
  .card-back { left: 600px; top: 470px; }
  .band { position: absolute; left: 0; bottom: 0; width: 100%; }
  .card-front .band { height: 82px; }
  .card-back .band { height: 90px; }

  /* front */
  .brand {
    position: absolute; top: 22px; left: 0; width: 100%;
    text-align: center;
  }
  .brand-name {
    font-family: "Russo One", sans-serif;
    font-size: 28px; color: var(--green); letter-spacing: 1px;
    display: inline-flex; align-items: center; gap: 10px;
  }
  .brand-dot { width: 16px; height: 16px; border-radius: 50%; background: var(--lime); display: inline-block; }
  .brand-tagline { font-size: 11px; margin-top: 4px; }
  .pitch {
    position: absolute; top: 92px; left: 0; width: 100%;
    text-align: center; font-size: 16px; line-height: 1.35;
  }
  .pitch-title {
    display: inline-block;
    border: 2px solid var(--ink); border-radius: 14px;
    padding: 3px 14px 1px; margin-bottom: 6px;
    font-weight: 600; font-size: 17px;
  }
  .accent { color: var(--lime); }
  .accent-bold { color: var(--lime); font-weight: 700; }
  .front-url {
    position: absolute; left: 26px; bottom: 8px;
    font-size: 15px; font-weight: 600; color: var(--ink);
  }

  /* back */
  .back-mark {
    position: absolute; left: 30px; top: 70px; width: 200px;
    text-align: center;
  }
  .back-mark .brand-name { font-size: 24px; flex-direction: column; gap: 8px; line-height: 1.15; }
  .back-mark .brand-dot { width: 34px; height: 34px; }
  .divider { position: absolute; left: 250px; top: 40px; width: 1px; height: 130px; background: var(--rule); }
  .contact { position: absolute; left: 272px; top: 36px; }
  .person-name { font-family: "Russo One", sans-serif; font-size: 24px; color: var(--lime); }
  .person-role { font-family: "Russo One", sans-serif; font-size: 13px; margin-bottom: 10px; }
  .contact-line { display: flex; align-items: center; gap: 10px; font-size: 16px; line-height: 1.45; }
  .contact-line svg { width: 14px; height: 14px; flex: none; }
  .offer {
    position: absolute; left: 0; width: 100%; bottom: 96px;
    text-align: center; font-size: 18px;
  }
  .offer .hot { font-family: "Russo One", sans-serif; color: var(--lime); font-size: 16px; }
  .offer .free { font-family: "Russo One", sans-serif; font-size: 16px; }
  .bullet { display: inline-block; width: 8px; height: 8px; border-radius: 50%; background: var(--ink); vertical-align: middle; margin: 0 10px; }
</style>
</head>
<body>

<section class="card card-front">
  <svg class="band" viewBox="0 0 540 82" preserveAspectRatio="none" aria-hidden="true">
    <polygon points="0,50 330,50 330,82 0,82" fill="var(--lime)"/>
    <polygon points="330,22 540,0 540,82 330,82" fill="var(--green)"/>
  </svg>
  <div class="brand">
    <div class="brand-name"><span class="brand-dot"></span>Steadfast Money Coaching</div>
    <div class="brand-tagline">Achieve a new level of personal freedom</div>
  </div>
  <div class="pitch">
    <div class="pitch-title"><span class="accent">STRUGGLING</span> WITH YOUR <span class="accent">FINANCES?</span></div>
    <p>Learn to become debt free</p>
    <p>Discover the power of cash</p>
    <p>Control your money instead of it controlling you</p>
    <p>Let us help you achieve a new level of financial <span class="accent-bold">FREEDOM!</span></p>
  </div>
  <div class="front-url">www.steadycoinplan.com</div>
</section>

<section class="card card-back">
  <svg class="band" viewBox="0 0 540 90" preserveAspectRatio="none" aria-hidden="true">
    <polygon points="0,72 540,50 540,90 0,90" fill="var(--lime)"/>
    <polygon points="330,30 540,8 540,51 330,60" fill="var(--green)"/>
  </svg>
  <div class="back-mark">
    <div class="brand-name"><span class="brand-dot"></span>Steadfast<br>Money Coaching</div>
  </div>
  <div class="divider"></div>
  <div class="contact">
    <div class="person-name">NORA K. WHITFIELD</div>
    <div class="person-role">PERSONAL FINANCIAL COACH</div>
    <div class="contact-line">
      <svg viewBox="0 0 14 14" aria-hidden="true"><rect x="3.5" y="1" width="7" height="12" rx="1.5" fill="none" stroke="var(--lime)" stroke-width="1.5"/><circle cx="7" cy="10.5" r="0.9" fill="var(--lime)"/></svg>
      <span>(555) 014-2270</span>
    </div>
    <div class="contact-line">
      <svg viewBox="0 0 14 14" aria-hidden="true"><rect x="1" y="3" width="12" height="8" fill="none" stroke="var(--lime)" stroke-width="1.5"/><polyline points="1,3 7,8 13,3" fill="none" stroke="var(--lime)" stroke-width="1.5"/></svg>
      <span>nora@steadycoinplan.com</span>
    </div>
    <div class="contact-line">
      <svg viewBox="0 0 14 14" aria-hidden="true"><circle cx="7" cy="7" r="5.5" fill="none" stroke="var(--lime)" stroke-width="1.4"/><ellipse cx="7" cy="7" rx="2.3" ry="5.5" fill="none" stroke="var(--lime)" stroke-width="1.2"/><line x1="1.5" y1="7" x2="12.5" y2="7" stroke="var(--lime)" stroke-width="1.2"/></svg>
      <span>www.<span class="accent">steadycoinplan</span>.com</span>
    </div>
  </div>
  <div class="offer">
    <span class="bullet"></span><span class="hot">SPECIAL OFFER!</span> <span class="free">FREE</span> 30 <span class="accent">minute consultation</span><span class="bullet"></span>
  </div>
</section>

</body>
</html>
```